Poetry Book Cover Design Project

Looking for a minimalistic book cover design for a collection of poems. The book title is "Before The Lanterns Drift Away Slowly". There are three parts to the book. First covers poetry in the theme of Rage. Second love and desire. The third is strange poems. Essentially the sections are "Rage", "Desire" and the "Strange". The reason for the title "Before The Lanterns Drift Away Slowly" is as if someone is writing these till life changes towards the intended outcome as felt in each poem. I want to have the author's name "Ruvinath Kolongaswe" at the bottom. Ilustration attached.
- Minimalistic

```html
<!DOCTYPE html>
<html lang="en">
<head>
<meta charset="utf-8">
<title>Before The Lanterns Drift Away Slowly — Ruvinath Kolongaswe</title>
<link rel="stylesheet" href="https://fonts.googleapis.com/css2?family=Libre+Baskerville:wght@700&display=swap">
<style>
  :root {
    --teal-light: #6cc3b8;
    --teal-mid: #2f8f99;
    --teal-deep: #0f4a58;
    --ink-dark: #0a2530;
    --copper: #c4582a;
    --copper-dark: #6e2c17;
    --title-white: #f4fbff;
    --title-blue: #9fd8f5;
    --author-white: #ffffff;
  }
  * { margin: 0; padding: 0; box-sizing: border-box; }
  html, body {
    width: 810px;
    height: 1200px;
    overflow: hidden;
    background: var(--ink-dark);
  }
  .cover {
    position: relative;
    width: 810px;
    height: 1200px;
    overflow: hidden;
    font-family: "Libre Baskerville", "Baskerville", Georgia, serif;
  }
  .cover-artwork {
    position: absolute;
    inset: 0;
    background:
      radial-gradient(ellipse 260px 520px at 40px 760px, rgba(196, 88, 42, 0.85), transparent 70%),
      radial-gradient(ellipse 420px 260px at 330px 1130px, rgba(196, 88, 42, 0.7), transparent 70%),
      radial-gradient(ellipse 260px 200px at 640px 1050px, rgba(180, 80, 40, 0.55), transparent 70%),
      radial-gradient(ellipse 320px 380px at 700px 620px, rgba(108, 195, 184, 0.55), transparent 70%),
      radial-gradient(ellipse 520px 420px at 320px 130px, var(--teal-light), transparent 75%),
      linear-gradient(180deg, var(--teal-mid) 0%, #2a7f8c 38%, var(--teal-deep) 62%, var(--ink-dark) 85%, #1a1d1f 100%);
  }
  .title {
    position: absolute;
    right: 60px;
    top: 52px;
    text-align: right;
    font-weight: 700;
    font-size: 118px;
    line-height: 112px;
    letter-spacing: -1px;
    background: linear-gradient(115deg, var(--title-white) 0%, var(--title-white) 40%, var(--title-blue) 75%, var(--title-white) 100%);
    -webkit-background-clip: text;
    background-clip: text;
    color: transparent;
  }
  .title-line { display: block; }
  .author {
    position: absolute;
    left: 0;
    right: 0;
    top: 1120px;
    text-align: center;
    padding-left: 4px;
    font-weight: 700;
    font-size: 31px;
    letter-spacing: -0.3px;
    color: var(--author-white);
  }
</style>
</head>
<body>
  <main class="cover">
    <div class="cover-artwork" role="img" aria-label="Abstract fluid artwork of teal and deep blue tones streaked with copper-orange pigment"></div>
    <h1 class="title">
      <span class="title-line">Before</span>
      <span class="title-line">The</span>
      <span class="title-line">Lanterns</span>
      <span class="title-line">Drift</span>
      <span class="title-line">Away</span>
      <span class="title-line">Slowly</span>
    </h1>
    <p class="author">Ruvinath Kolongaswe</p>
  </main>
</body>
</html>
```